New Zealand Marlborough Sauvignon Blanc wine packaging design

We need packaging design for our new wine brand, Dunmore Vale. The wine is a New Zealand Marlborough Sauvignon Blanc. We would like the packaging will portray elegance and style with an understated label. We are looking for a label that portrays the elegance of the French Riviera. The label should be round or pill shaped.
Updates

Industry/Entity Type

Wine

Font styles to use
Serif
Sans Serif

Requirements
Must have
• The words in order of importance: Dunmore Vale, Sauvignon Blanc, Marlborough, New Zealand. It should be fit to the bottle posted in the links
Nice to have
• a pill shape or circular shape
Should not have
• Illustrations of wine bottles, wine glasses, or grapes

```html
<!DOCTYPE html>
<html lang="en">
<head>
<meta charset="UTF-8">
<title>Dunmore Vale — Marlborough Sauvignon Blanc Label</title>
<link rel="stylesheet" href="https://fonts.googleapis.com/css2?family=Jost:wght@500&family=Marcellus&display=swap">
<style>
  :root {
    --ground: #000000;
    --ink: #ffffff;
    --sky-peach: #f3c58f;
    --sky-blue: #8fb6d6;
    --hills: #5f8fa8;
    --lagoon: #3ea7b0;
    --deep-water: #1f5f8c;
    --sand: #e9a55a;
  }
  * { margin: 0; padding: 0; box-sizing: border-box; }
  html, body {
    width: 705px;
    height: 1200px;
    overflow: hidden;
    background: var(--ground);
  }
  .label {
    position: relative;
    width: 705px;
    height: 1200px;
  }
  .label-art {
    position: absolute;
    inset: 0;
  }
  .ring-text {
    font-family: "Jost", sans-serif;
    font-weight: 500;
    font-size: 33px;
    letter-spacing: 0.2em;
    fill: var(--ink);
  }
  .brand-name {
    position: absolute;
    left: 0;
    right: 0;
    top: 520px;
    text-align: center;
    font-family: "Marcellus", serif;
    font-size: 78px;
    line-height: 76px;
    color: var(--ink);
    letter-spacing: 0.01em;
  }
</style>
</head>
<body>
  <main class="label">
    <svg class="label-art" width="705" height="1200" viewBox="0 0 705 1200" xmlns="http://www.w3.org/2000/svg">
      <defs>
        <linearGradient id="scene-tones" x1="0" y1="0" x2="0.35" y2="1">
          <stop offset="0" stop-color="var(--sky-blue)"/>
          <stop offset="0.18" stop-color="var(--sky-peach)"/>
          <stop offset="0.36" stop-color="var(--hills)"/>
          <stop offset="0.55" stop-color="var(--lagoon)"/>
          <stop offset="0.78" stop-color="var(--deep-water)"/>
          <stop offset="1" stop-color="var(--sand)"/>
        </linearGradient>
        <path id="arc-top" d="M 72 600 A 280 350 0 0 1 632 600"/>
        <path id="arc-bottom" d="M 58 600 A 294 386 0 0 0 646 600"/>
      </defs>

      <ellipse class="scene-painting" cx="352" cy="600" rx="255" ry="311"
               fill="url(#scene-tones)" role="img"
               aria-label="Painted coastal landscape: peach clouds over blue hills, a turquoise bay and sandy shore"/>

      <text class="ring-text" text-anchor="middle">
        <textPath href="#arc-top" startOffset="50%">NEW ZEALAND MARLBOROUGH</textPath>
      </text>
      <text class="ring-text" text-anchor="middle">
        <textPath href="#arc-bottom" startOffset="50%">SAUVIGNON BLANC</textPath>
      </text>
    </svg>

    <h1 class="brand-name">DUNMORE<br>VALE</h1>
  </main>
</body>
</html>
```